Social Media Graphics - Oakline Push REVISED

Create 6-7 individual social media graphics (square size) to encourage folks to join our online course called:

The Harvest Ledger Circle
How to Launch a Multi-Million Business From Scratch
Sign Up Today!

IMPORTANT: Make the largest and most prominent text on the graphic be: How to Launch a Multi-Million Business From Scratch

For the color scheme of the graphics, let's try a blue color palette; make sure the graphics appeal to both men and women

Make sure each graphic contains 1 of the 3 pics attached (crop pic as needed); and make sure one of the graphics is all TEXT only.

Target Market(s)

men and women looking to start a business

Industry/Entity Type

Entrepreneurship

Colors
0054AA
0677BA
7BADD7
CADEEF
E8F1F8

Requirements
Must have
• All the text and use the 3 pics provided; one graphic can be all text; Simple, modern design that's easy to read

```html
<!DOCTYPE html>
<html lang="en">
<head>
<meta charset="utf-8">
<title>The Harvest Ledger Circle – Social Graphic</title>
<link href="https://fonts.googleapis.com/css2?family=Archivo+Black&display=swap" rel="stylesheet">
<style>
  :root {
    --navy: #262c62;
    --deep-blue: #003f7f;
    --brand-blue: #0054aa;
    --mid-blue: #0677ba;
    --bright-cyan: #2ed0f0;
    --sky: #7badd7;
    --pale: #cadeef;
    --mist: #e8f1f8;
    --white: #ffffff;
    --ink-outline: #2a2a2a;
  }
  html, body {
    margin: 0;
    padding: 0;
    width: 1200px;
    height: 1200px;
    overflow: hidden;
    background: var(--white);
  }
  .graphic {
    position: relative;
    width: 1200px;
    height: 1200px;
    overflow: hidden;
    font-family: "Archivo Black", "Arial Black", sans-serif;
  }
  .graphic__backdrop {
    position: absolute;
    inset: 0;
  }
  .speaker-photo {
    position: absolute;
    left: 300px;
    top: 40px;
    width: 700px;
    height: 555px;
    border-radius: 260px 260px 0 0;
    background: linear-gradient(180deg, rgba(123,173,215,0.55) 0%, rgba(202,222,239,0.75) 55%, rgba(232,241,248,0.2) 100%);
  }
  .course-name {
    position: absolute;
    left: 264px;
    top: 592px;
    width: 671px;
    height: 66px;
    border-radius: 33px;
    background: linear-gradient(90deg, #25207a 0%, var(--mid-blue) 55%, #1f2a80 100%);
    color: var(--white);
    display: flex;
    align-items: center;
    justify-content: center;
    font-size: 34px;
    letter-spacing: 0.5px;
    text-transform: uppercase;
    white-space: nowrap;
  }
  .headline {
    position: absolute;
    left: 134px;
    right: 144px;
    top: 683px;
    margin: 0;
    text-align: center;
    color: var(--white);
    font-size: 84px;
    line-height: 87px;
    font-weight: 400;
    text-transform: uppercase;
    letter-spacing: 1px;
    -webkit-text-stroke: 3px var(--ink-outline);
    paint-order: stroke fill;
  }
  .cta-button {
    position: absolute;
    left: 357px;
    top: 1068px;
    width: 488px;
    height: 74px;
    border-radius: 37px;
    background: linear-gradient(180deg, #46b6cf 0%, #2a96e8 100%);
    color: var(--white);
    display: flex;
    align-items: center;
    justify-content: center;
    font-size: 40px;
    text-transform: uppercase;
    letter-spacing: 0.5px;
  }
</style>
</head>
<body>
<main class="graphic">
  <svg class="graphic__backdrop" width="1200" height="1200" viewBox="0 0 1200 1200" aria-hidden="true">
    <defs>
      <radialGradient id="bg-glow" cx="0.78" cy="0.24" r="0.9">
        <stop offset="0" stop-color="#2ed0f0"/>
        <stop offset="0.25" stop-color="#0a86d8"/>
        <stop offset="0.6" stop-color="#0a5fae"/>
        <stop offset="1" stop-color="#003f7f"/>
      </radialGradient>
      <linearGradient id="disc-fill" x1="0" y1="0" x2="0" y2="1">
        <stop offset="0" stop-color="#ffffff"/>
        <stop offset="0.45" stop-color="#cadeef"/>
        <stop offset="1" stop-color="#7badd7"/>
      </linearGradient>
    </defs>
    <rect width="1200" height="1200" fill="url(#bg-glow)"/>
    <rect x="1" y="1" width="1198" height="1198" fill="none" stroke="#f1ead8" stroke-width="3"/>
    <line x1="8" y1="8" x2="272" y2="272" stroke="#ffffff" stroke-width="3"/>
    <line x1="1192" y1="8" x2="928" y2="278" stroke="#ffffff" stroke-width="3"/>
    <circle cx="593" cy="605" r="466" fill="url(#disc-fill)" stroke="#3fa7c9" stroke-width="3"/>
    <line x1="272" y1="272" x2="400" y2="400" stroke="#ffffff" stroke-opacity="0.6" stroke-width="2"/>
    <line x1="928" y1="278" x2="800" y2="400" stroke="#ffffff" stroke-opacity="0.6" stroke-width="2"/>
    <circle cx="593" cy="605" r="368" fill="none" stroke="#ffffff" stroke-width="3"/>
    <path d="M 170 661 L 1020 661 Q 1052 661 1060 692 L 1196 1200 L 4 1200 L 134 692 Q 142 661 170 661 Z"
          fill="#262c62" stroke="#ffffff" stroke-width="3"/>
  </svg>

  <div class="speaker-photo" role="img" aria-label="Photo of two smiling course hosts, a woman in a blue blazer and a man in a grey blazer speaking into a microphone"></div>

  <div class="course-name">The Harvest Ledger Circle</div>

  <h1 class="headline">How to Launch<br>A Multi-Million<br>Business From<br>Scratch</h1>

  <div class="cta-button">Sign Up Today!</div>
</main>
</body>
</html>
```